Logo and Website Design for QR.KA Horizon - a Software Engineering and IT company

Software engineering and IT are two different disciplines - and yet inseparably linked. At QR.KA Horizon, we combine both worlds and ensure that our software solutions are not only innovative and powerful, but also integrate perfectly into existing IT landscapes. Vision stands more for imagination, so it is not neccessary something what has to do with visualisation. Please consider that the winning competitor is also instructed to make a logo for the company. So please make a suitable logo for QR.KA Horizon to which the website fits to and show it during the website creation process. A good Logo desing is important for winning the competition. The website should contain a landing page with inspiring, perhaps futuristic photos of a datacenter and lines of code. Eventuelly flewent integrated in the text. On the landing page the company should introduced with a small text (max 250 words) followed by a section with a short text to one of our products nearby a graphic visualising the architecture of the product. The menue should be on top and fixed during scrolling and consist of the menue items home, solutions, who are we and a contact button. There should be a footer for linking social media, rights and Impressum. Only as an idea not a must. The very first view on the landing page could also be the menue bar and below of it a transparent unsharp photo (e.g. datacenter, lines of code, both ;) with the company name in the center.

###############################################################

Hi Designers,

Despite your very good approaches for describing QR.KA Horizon, here a short introduction (german text) from ourself:

------
QR.KA Horizon – Ihr Partner für ganzheitliche Softwarelösungen

Die QR.KA Horizon ist ein dynamisches Unternehmen, das sich nicht nur auf die Konzeption, das Design und die Entwicklung maßgeschneiderter Software spezialisiert hat, sondern auch deren reibungslosen Betrieb sicherstellt. Mit einem Team aus erfahrenen Softwarearchitekten und IT-Professionals verbinden wir modernste Softwareentwicklung mit tiefgehendem IT-Know-how – für Lösungen, die nachhaltig, leistungsstark und zukunftssicher sind.

Software Engineering trifft IT – Perfektion in Kombination
Software Engineering und IT sind zwei unterschiedliche Disziplinen – und doch untrennbar miteinander verbunden. Wir bei QR.KA Horizon vereinen beide Welten und sorgen dafür, dass unsere Softwarelösungen nicht nur innovativ und leistungsfähig sind, sondern sich auch perfekt in bestehende IT-Landschaften integrieren.

Expertise mit Fokus auf Healthcare & komplexe IT-Umgebungen
Unsere Experten bringen jahrzehntelange Erfahrung aus dem Healthcare-Sektor mit und unterstützen IT-Abteilungen großer Kliniken in der Entwicklung und Optimierung von Softwarelösungen. Von Anwendungssoftware bis hin zu Steuerungssystemen – unsere Softwareingenieure wissen genau, worauf es ankommt.

Ganzheitlicher Ansatz – über die Software hinaus
Wir entwickeln nicht nur Software, sondern übernehmen auch die Verantwortung für deren stabile und effiziente Betriebsumgebung. Egal, ob on-premises, in der Cloud oder als SaaS-Lösung – wir kümmern uns um den kompletten Lifecycle Ihrer Anwendung.

Ihre Vision – unsere Mission.
Ob Neuentwicklung einer SaaS-Anwendung oder die Migration bestehender Lösungen in eine moderne SaaS-Umgebung – mit QR.KA Horizon haben Sie einen starken Partner an Ihrer Seite.

Lassen Sie uns gemeinsam die Zukunft Ihrer Software gestalten!
--------------

Our first solution called "Clear Record Transfer Gateway" (CLURA)
-------------------
Teilen Sie Ihre Daten sicher – ohne Kompromisse!

Sie nutzen eine relationale Datenbank (Brightcask, Tabulon Hub, Vellumdb etc.) und möchten ausgewählte Daten mit Dritten teilen – sei es für ein Data Warehouse, Business Controller, Lieferanten oder Kunden? Doch dabei sollen Datensicherheit, Integrität und Verfügbarkeit Ihrer primären Lösung in keiner Weise gefährdet werden?

Mit unserer Lösung erhalten Sie genau das: Maximalen Schutz für Ihre Anwendung bei gleichzeitigem Nutzen durch autorisierte Dritte – ganz ohne teure Lizenzkosten für eine Schattendatenbank.

Lassen Sie uns gemeinsam herausfinden, wie Sie Ihre Daten sicher und effizient nutzen können. Kontaktieren Sie uns – wir zeigen Ihnen, was möglich ist!
---------------------

Our second solution MIVO:
---------------------
MIVO – Program for a Tone Matching Instrument ist die smarte Lösung für Unternehmen, die bei Farbgenauigkeit keine Kompromisse machen. Die Software erkennt Farbabweichungen zwischen Mustern vollautomatisch, beschreibt sie verständlich und sorgt so für gleichbleibend hohe Produktqualität – schnell, visuell und präzise. Perfekt für alle, die Farbe zur Vertrauenssache machen.
-------------------------

Thanks,
Gerold

Target Market(s)

IT Professionals from any sector

Industry/Entity Type

Healthcare and other

Coding

Coded - Design and coding required

Number of Pages Required

1 page

Font styles to use
Sans Serif

Colors
0054AA
0677BA
7BADD7
CADEEF
E8F1F8
0094D4
00A9DD
6FCCEA
C7EBF8
E9F6FB
00AB8E
00BBA5
67D7C9
C6EFE9
E9F9F6

Requirements
Must have
• Please see description
Nice to have
• On the landing page the company should introduced with a small text (max 250 words) followed by a section with a short text to one of our products nearby a graphic visualising the architecture of the product. The menue should be on top and fixed during scrolling and consist of the menue items home, solutions, who are we and a contact button. There should be a footer for linking social media, rights and Impressum. Only as an idea not a must. The very first view on the landing page could also be the menue bar and below of it a transparent unsharp photo (e.g. datacenter, lines of code, both ;) with the company name in the center.
Should not have
• Please see description

```html
<!DOCTYPE html>
<html lang="en">
<head>
<meta charset="utf-8">
<title>QR.KA Horizon – Website Concepts</title>
<link href="https://fonts.googleapis.com/css2?family=Lato:wght@300;400;700;900&family=Roboto:wght@400;500;700&display=swap" rel="stylesheet">
<style>
:root{
  --stage:#808080;
  --navy:#0054AA;
  --blue:#0094D4;
  --blue-deep:#0677BA;
  --sky:#6FCCEA;
  --pale:#E8F1F8;
  --pale-2:#CADEEF;
  --soft:#7BADD7;
  --white:#FFFFFF;
  --ink:#141414;
  --text:#6a6f76;
  --footer:#0d0d0f;
  --footer-text:#c9cdd3;
}
*{box-sizing:border-box;margin:0;padding:0}
html,body{width:1189px;height:1200px;overflow:hidden}
body{background:var(--stage);position:relative;font-family:'Roboto',Arial,sans-serif}
.page{position:absolute;top:35px;width:551px;height:1818px;background:var(--pale);transform:scale(0.6215);transform-origin:0 0;overflow:hidden}
.page--one{left:48px}
.page--two{left:420px}
.page--three{left:799px}
.hero{position:absolute;left:0;top:0;width:551px;height:320px}
.page--one .hero{background:
  radial-gradient(ellipse 90px 70px at 275px 280px,#2a4f7a 0%,rgba(20,40,70,0) 100%),
  radial-gradient(ellipse 160px 220px at 275px 120px,#3b6fa6 0%,rgba(30,60,100,0) 100%),
  linear-gradient(90deg,#0b1a33 0%,#14345e 25%,#1d4a7c 50%,#14345e 75%,#0b1a33 100%)}
.page--two .hero{background:
  radial-gradient(ellipse 130px 150px at 130px 170px,#2b5c8c 0%,rgba(20,50,80,0) 100%),
  radial-gradient(ellipse 120px 250px at 480px 150px,#1f6d9a 0%,rgba(20,60,90,0) 100%),
  linear-gradient(90deg,#0f1f33 0%,#1a3350 40%,#203e5e 60%,#0e2a45 100%)}
.page--three .hero{background:
  radial-gradient(ellipse 220px 120px at 400px 180px,#1c6a93 0%,rgba(10,40,70,0) 100%),
  radial-gradient(ellipse 120px 90px at 470px 240px,#2f86a8 0%,rgba(20,60,90,0) 100%),
  linear-gradient(90deg,#081426 0%,#0d2340 45%,#113052 100%)}
.bands{position:absolute;left:0;top:0}
.nav-logo{position:absolute;left:48px;top:12px;display:flex;align-items:center;gap:5px}
.logo-mark{width:14px;height:14px;background:var(--blue)}
.logo-name{font-family:'Lato',Arial,sans-serif;font-weight:700;font-size:13px;color:var(--white);letter-spacing:-.2px;white-space:nowrap}
.nav-menu{position:absolute;top:16px;font-family:'Roboto',Arial,sans-serif;font-weight:700;font-size:6px;color:var(--white);letter-spacing:.2px;white-space:nowrap}
.nav-menu--home{left:265px;color:var(--sky)}
.nav-menu--solutions{left:304px}
.nav-menu--who{left:362px}
.btn{position:absolute;background:var(--blue);color:var(--white);font-family:'Roboto',Arial,sans-serif;font-weight:700;font-size:6px;letter-spacing:.3px;display:flex;align-items:center;justify-content:center;gap:3px;white-space:nowrap}
.btn--contact{left:425px;top:10px;width:74px;height:21px}
.btn-dot{width:6px;height:6px;border-radius:50%;background:var(--white);position:relative}
.btn-dot::after{content:"";position:absolute;left:2px;top:1.6px;border-left:2px solid var(--blue);border-top:1.4px solid transparent;border-bottom:1.4px solid transparent}
.hero-copy{position:absolute}
.hero-title{font-family:'Lato',Arial,sans-serif;font-weight:900;font-size:25px;color:var(--white);letter-spacing:-.3px;white-space:nowrap}
.hero-sub{font-family:'Roboto',Arial,sans-serif;font-weight:500;font-size:6.6px;color:var(--white);line-height:12px}
.btn--hero{width:89px;height:23px}
.page--one .hero-copy{left:0;width:551px;top:70px;text-align:center}
.page--one .hero-sub{margin-top:2px}
.page--one .btn--hero{left:231px;top:57px}
.page--two .hero-copy{left:300px;top:104px;width:190px}
.page--two .hero-sub{margin-top:4px}
.page--two .btn--hero{left:0;top:70px}
.page--three .hero-copy{left:51px;top:100px;width:170px}
.page--three .hero-sub{margin-top:4px}
.page--three .btn--hero{left:0;top:75px}
.section-title{position:absolute;font-family:'Lato',Arial,sans-serif;font-size:17.5px;white-space:nowrap;letter-spacing:-.2px}
.section-title .light{font-weight:300;color:var(--navy)}
.section-title .bold{font-weight:900;color:var(--ink)}
.section-title--inverse .light,.section-title--inverse .bold{color:var(--white)}
.rule{position:absolute;height:2px;width:36px;background:var(--blue)}
.rule--inverse{background:var(--white)}
.copy{position:absolute;font-size:5.4px;line-height:9.6px;color:var(--text)}
.copy p+p{margin-top:4.4px}
.copy--center{text-align:center}
.architecture-graphic{position:absolute;left:68px;top:533px;width:172px;height:227px;border-radius:8px;background:linear-gradient(180deg,var(--pale) 0%,var(--pale-2) 100%)}
.btn--learn{width:74px;height:20px}
.solution{position:absolute;width:220px;text-align:center;color:var(--white)}
.solution-icon{width:44px;height:44px;border-radius:50%;background:var(--white);margin:0 auto;display:flex;align-items:center;justify-content:center}
.solution-title{font-family:'Roboto',Arial,sans-serif;font-weight:700;font-size:7px;margin-top:13px}
.solution-text{font-size:5.4px;line-height:9.6px;margin-top:6px}
.solution-link{font-weight:700;font-size:5.6px;margin-top:7px;text-decoration:underline;display:flex;justify-content:center;align-items:center;gap:3px}
.divider{position:absolute;left:276px;top:894px;width:1px;height:131px;background:rgba(255,255,255,.6)}
.who-photo{position:absolute;left:302px;top:1115px;width:196px;height:196px;border-radius:50%;border:1px solid var(--blue);display:flex;align-items:center;justify-content:center}
.who-photo-inner{width:180px;height:180px;border-radius:50%;border:3px solid var(--white);box-shadow:0 0 0 1px var(--blue);background:
  radial-gradient(ellipse 40px 90px at 90px 90px,#b9d9ef 0%,rgba(90,150,200,0) 100%),
  linear-gradient(90deg,#0f2340 0%,#1e5b8e 25%,#4d9ccc 45%,#e3b25a 55%,#1b4d7c 75%,#0c1f3a 100%)}
.field{position:absolute;background:var(--white);height:23px;font-size:5.4px;color:#9aa0a8;padding:9px 0 0 9px}
.field--message{height:41px}
.footer-logo{position:absolute;left:48px;top:1690px;display:flex;align-items:center;gap:5px}
.socials{position:absolute;left:76px;top:1723px;display:flex;gap:4px}
.social{width:14px;height:14px;border-radius:50%;background:var(--white)}
.social--active{background:var(--blue)}
.foot-col{position:absolute;color:var(--footer-text);font-size:5px;line-height:11.8px}
.foot-head{font-family:'Roboto',Arial,sans-serif;font-weight:700;font-size:6.4px;color:var(--white);margin-bottom:5px;line-height:9px}
.contact-item{position:relative;padding-left:10px;line-height:8.4px;margin-bottom:5px}
.contact-item b{color:var(--white);font-weight:700;font-size:4.8px}
.contact-item svg{position:absolute;left:0;top:0}
.to-top{position:absolute;left:520px;top:1749px;width:16px;height:16px;border-radius:50%;background:var(--blue);display:flex;align-items:center;justify-content:center}
.foot-rule{position:absolute;left:48px;top:1783px;width:455px;height:1px;background:#2a2c30}
.copyright{position:absolute;left:0;width:551px;top:1796px;text-align:center;font-size:5.4px;color:var(--footer-text)}
</style>
</head>
<body>

<section class="page page--one">
  <div class="hero" role="img" aria-label="Photo of a data centre aisle with a laptop showing lines of code"></div>
  <svg class="bands" width="551" height="1818" viewBox="0 0 551 1818" aria-hidden="true">
    <path d="M0 263 Q275.5 343 551 263 V330 H0Z" fill="#E8F1F8"/>
    <path d="M0 518 Q275.5 438 551 518 V783 Q275.5 859 0 783Z" fill="#FFFFFF"/>
    <path d="M0 783 Q275.5 859 551 783 V1103 Q275.5 1019 0 1103Z" fill="#0591D3"/>
    <path d="M0 1103 Q275.5 1019 551 1103 V1323 Q275.5 1403 0 1323Z" fill="#FFFFFF"/>
    <path d="M0 1670 Q275.5 1590 551 1670 V1818 H0Z" fill="#0d0d0f"/>
  </svg>
  <div class="nav-logo"><span class="logo-mark"></span><span class="logo-name">QR.KA HORIZON</span></div>
  <span class="nav-menu nav-menu--home">HOME</span>
  <span class="nav-menu nav-menu--solutions">SOLUTIONS</span>
  <span class="nav-menu nav-menu--who">WHO ARE WE</span>
  <span class="btn btn--contact">CONTACT US</span>
  <div class="hero-copy">
    <h1 class="hero-title">QR.KA HORIZON</h1>
    <p class="hero-sub">Bridging Imagination, Software Engineering, and IT Infrastructure</p>
    <span class="btn btn--hero">GET STARTED <span class="btn-dot"></span></span>
  </div>
  <h2 class="section-title" style="left:0;width:551px;text-align:center;top:331px"><span class="light">WELCOME</span> <span class="bold">TO QR.KA HORIZON</span></h2>
  <div class="copy copy--center" style="left:66px;top:376px;width:419px">
    <p>QR.KA Horizon is where imagination meets execution. We unify the disciplines of software engineering and IT to deliver robust, future-oriented software solutions that are seamlessly integrated into diverse IT ecosystems.</p>
    <p>Our team thrives at the intersection of precision engineering and visionary architecture, ensuring every project is tailored, scalable, and secure. Whether optimizing legacy systems or deploying greenfield architectures, we believe that technology should not only work – it should inspire.</p>
    <p>At QR.KA Horizon, “Horizon” isn't about what you see — it's about what you imagine. Let's build the future together.</p>
  </div>
  <div class="architecture-graphic" role="img" aria-label="Architecture graphic of the ORBIT Layer product linking client apps, gateway, data lake, microservices and enterprise IT"></div>
  <h2 class="section-title" style="left:276px;top:537px"><span class="light">OUR</span> <span class="bold">PRODUCTS</span></h2>
  <span class="rule" style="left:276px;top:564px"></span>
  <div class="copy" style="left:275px;top:586px;width:226px">
    <p>ORBIT Layer™ is our flagship middleware that seamlessly connects diverse systems, enabling real-time data flow and business process synchronization.</p>
    <p>Whether cloud-native or hybrid, ORBIT adapts intelligently to your environment — secure, efficient, and built to scale.</p>
    <p>Introducing **FluxLink**, our modular architecture for synchronizing real-time data across hybrid systems.</p>
    <p>FluxLink allows seamless integration of microservices, legacy systems, and cloud platforms. It's scalable, resilient, and purpose-built to evolve with your IT ecosystem.</p>
  </div>
  <span class="btn btn--learn" style="left:275px;top:732px">LEARN MORE</span>
  <h2 class="section-title section-title--inverse" style="left:0;width:551px;text-align:center;top:846px"><span class="light">OUR</span> <span class="bold">SOLUTIONS</span></h2>
  <span class="rule rule--inverse" style="left:257px;top:873px"></span>
  <div class="solution" style="left:40px;top:894px">
    <div class="solution-icon"><svg width="26" height="26" viewBox="0 0 26 26" fill="none" stroke="#0054AA" stroke-width="1.2"><path d="M7 18 h12 a4 4 0 0 0 0-8 a6 6 0 0 0-11-1 a4.5 4.5 0 0 0-1 9z"/><circle cx="13" cy="14" r="3"/></svg></div>
    <div class="solution-title">Software-Defined Integration</div>
    <div class="solution-text">Lorem ipsum dolor sit amet, consectetur adipiscing elit, sed do eiusmod tempor incididunt ut labore et dolore magna aliqua. Ut enim ad ex ea commodo consequat.</div>
    <div class="solution-link">LEARN MORE <span class="btn-dot"></span></div>
  </div>
  <span class="divider"></span>
  <div class="solution" style="left:290px;top:894px">
    <div class="solution-icon"><svg width="26" height="26" viewBox="0 0 26 26" fill="none" stroke="#0054AA" stroke-width="1.2"><rect x="6" y="8" width="14" height="12" rx="1.5"/><circle cx="13" cy="14" r="3"/><path d="M9 8 V4 M17 8 V4 M4 12 H6 M20 12 H22"/></svg></div>
    <div class="solution-title">Modular Platforms</div>
    <div class="solution-text">Lorem ipsum dolor sit amet, consectetur adipiscing elit, sed do eiusmod tempor incididunt ut labore et dolore magna aliqua. Ut enim ad ex ea commodo consequat.</div>
    <div class="solution-link">LEARN MORE <span class="btn-dot"></span></div>
  </div>
  <h2 class="section-title" style="left:51px;top:1132px"><span class="light">WHO</span> <span class="bold">ARE WE</span></h2>
  <span class="rule" style="left:51px;top:1158px"></span>
  <div class="copy" style="left:51px;top:1179px;width:220px">
    <p>We are engineers, architects, and technologists with a shared purpose: to align software precision with IT reality.</p>
    <p>Our team brings decades of experience in enterprise architecture, system integration, and software engineering. We believe technology should be both powerful and practical — imaginative yet grounded.</p>
    <p>Our DNA? Curiosity, clarity, and a relentless drive for quality.</p>
  </div>
  <span class="btn btn--learn" style="left:51px;top:1270px">LEARN MORE</span>
  <div class="who-photo"><div class="who-photo-inner" role="img" aria-label="Photo of illuminated server racks in a data centre"></div></div>
  <h2 class="section-title" style="left:0;width:551px;text-align:center;top:1393px"><span class="light">CONTACT</span> <span class="bold">US</span></h2>
  <div class="field" style="left:85px;top:1443px;width:187px">First Name *</div>
  <div class="field" style="left:279px;top:1443px;width:187px">Last Name *</div>
  <div class="field" style="left:85px;top:1473px;width:187px">Phone Number *</div>
  <div class="field" style="left:279px;top:1473px;width:187px">Email Address *</div>
  <div class="field field--message" style="left:85px;top:1505px;width:381px">Message</div>
  <span class="btn" style="left:239px;top:1567px;width:73px;height:21px">SUBMIT NOW</span>
  <div class="footer-logo"><span class="logo-mark"></span><span class="logo-name">QR.KA HORIZON</span></div>
  <div class="socials"><span class="social"></span><span class="social social--active"></span><span class="social"></span><span class="social"></span></div>
  <div class="foot-col" style="left:206px;top:1674px"><div class="foot-head">Quick Links</div>About<br>Products<br>Brands<br>Services<br>Contact</div>
  <div class="foot-col" style="left:289px;top:1674px"><div class="foot-head">About Company</div>GDPR<br>Privacy Policy<br>Cookie Policy<br>Terms &amp; Condition<br>Support</div>
  <div class="foot-col" style="left:389px;top:1674px;width:120px">
    <div class="foot-head">Contact Us</div>
    <div class="contact-item"><svg width="6" height="7" viewBox="0 0 6 7"><path d="M3 0.5a2.3 2.3 0 0 1 2.3 2.3C5.3 4.5 3 6.5 3 6.5S0.7 4.5 0.7 2.8A2.3 2.3 0 0 1 3 0.5z" fill="#0094D4"/></svg><b>Location</b><br>88 Larkfield Road, Unit 4, Brookhaven,<br>ST 20417</div>
    <div class="contact-item"><svg width="6" height="6" viewBox="0 0 6 6"><path d="M1 0.5 L2.2 0.5 L2.7 2 L2 2.6 Q2.7 3.6 3.4 4 L4 3.3 L5.5 3.8 L5.5 5 Q3 5.5 0.5 1.5z" fill="#0094D4"/></svg><b>Phone</b><br>+1 555 014 2290</div>
    <div class="contact-item"><svg width="6" height="5" viewBox="0 0 6 5"><rect x="0.3" y="0.5" width="5.4" height="4" fill="#0094D4"/><path d="M0.3 0.7 L3 2.7 L5.7 0.7" stroke="#0d0d0f" stroke-width="0.6" fill="none"/></svg><b>Email</b><br>info@qrkahorizon.example</div>
  </div>
  <span class="to-top"><svg width="7" height="5" viewBox="0 0 7 5"><path d="M1 4 L3.5 1.5 L6 4" stroke="#fff" stroke-width="1.2" fill="none"/></svg></span>
  <span class="foot-rule"></span>
  <p class="copyright">2025 Copyright - QR.KA Horizon. | All Rights Reserved</p>
</section>

<section class="page page--two">
  <div class="hero" role="img" aria-label="Photo of a laptop with lines of code beside a coffee cup in front of server racks"></div>
  <svg class="bands" width="551" height="1818" viewBox="0 0 551 1818" aria-hidden="true">
    <path d="M0 263 Q275.5 343 551 263 V330 H0Z" fill="#E8F1F8"/>
    <path d="M0 518 Q275.5 438 551 518 V783 Q275.5 859 0 783Z" fill="#FFFFFF"/>
    <path d="M0 783 Q275.5 859 551 783 V1103 Q275.5 1019 0 1103Z" fill="#0591D3"/>
    <path d="M0 1103 Q275.5 1019 551 1103 V1323 Q275.5 1403 0 1323Z" fill="#FFFFFF"/>
    <path d="M0 1670 Q275.5 1590 551 1670 V1818 H0Z" fill="#0d0d0f"/>
  </svg>
  <div class="nav-logo"><span class="logo-mark"></span><span class="logo-name">QR.KA HORIZON</span></div>
  <span class="nav-menu nav-menu--home">HOME</span>
  <span class="nav-menu nav-menu--solutions">SOLUTIONS</span>
  <span class="nav-menu nav-menu--who">WHO ARE WE</span>
  <span class="btn btn--contact">CONTACT US</span>
  <div class="hero-copy">
    <h1 class="hero-title">QR.KA HORIZON</h1>
    <p class="hero-sub">Bridging Imagination, Software Engineering, and IT Infrastructure</p>
    <span class="btn btn--hero">GET STARTED <span class="btn-dot"></span></span>
  </div>
  <h2 class="section-title" style="left:0;width:551px;text-align:center;top:331px"><span class="light">WELCOME</span> <span class="bold">TO QR.KA HORIZON</span></h2>
  <div class="copy copy--center" style="left:66px;top:376px;width:419px">
    <p>QR.KA Horizon is where imagination meets execution. We unify the disciplines of software engineering and IT to deliver robust, future-oriented software solutions that are seamlessly integrated into diverse IT ecosystems.</p>
    <p>Our team thrives at the intersection of precision engineering and visionary architecture, ensuring every project is tailored, scalable, and secure. Whether optimizing legacy systems or deploying greenfield architectures, we believe that technology should not only work – it should inspire.</p>
    <p>At QR.KA Horizon, “Horizon” isn't about what you see — it's about what you imagine. Let's build the future together.</p>
  </div>
  <div class="architecture-graphic" role="img" aria-label="Architecture graphic of the ORBIT Layer product linking client apps, gateway, data lake, microservices and enterprise IT"></div>
  <h2 class="section-title" style="left:276px;top:537px"><span class="light">OUR</span> <span class="bold">PRODUCTS</span></h2>
  <span class="rule" style="left:276px;top:564px"></span>
  <div class="copy" style="left:275px;top:586px;width:226px">
    <p>ORBIT Layer™ is our flagship middleware that seamlessly connects diverse systems, enabling real-time data flow and business process synchronization.</p>
    <p>Whether cloud-native or hybrid, ORBIT adapts intelligently to your environment — secure, efficient, and built to scale.</p>
    <p>Introducing **FluxLink**, our modular architecture for synchronizing real-time data across hybrid systems.</p>
    <p>FluxLink allows seamless integration of microservices, legacy systems, and cloud platforms. It's scalable, resilient, and purpose-built to evolve with your IT ecosystem.</p>
  </div>
  <span class="btn btn--learn" style="left:275px;top:732px">LEARN MORE</span>
  <h2 class="section-title section-title--inverse" style="left:0;width:551px;text-align:center;top:846px"><span class="light">OUR</span> <span class="bold">SOLUTIONS</span></h2>
  <span class="rule rule--inverse" style="left:257px;top:873px"></span>
  <div class="solution" style="left:40px;top:894px">
    <div class="solution-icon"><svg width="26" height="26" viewBox="0 0 26 26" fill="none" stroke="#0054AA" stroke-width="1.2"><path d="M7 18 h12 a4 4 0 0 0 0-8 a6 6 0 0 0-11-1 a4.5 4.5 0 0 0-1 9z"/><circle cx="13" cy="14" r="3"/></svg></div>
    <div class="solution-title">Software-Defined Integration</div>
    <div class="solution-text">Lorem ipsum dolor sit amet, consectetur adipiscing elit, sed do eiusmod tempor incididunt ut labore et dolore magna aliqua. Ut enim ad ex ea commodo consequat.</div>
    <div class="solution-link">LEARN MORE <span class="btn-dot"></span></div>
  </div>
  <span class="divider"></span>
  <div class="solution" style="left:290px;top:894px">
    <div class="solution-icon"><svg width="26" height="26" viewBox="0 0 26 26" fill="none" stroke="#0054AA" stroke-width="1.2"><rect x="6" y="8" width="14" height="12" rx="1.5"/><circle cx="13" cy="14" r="3"/><path d="M9 8 V4 M17 8 V4 M4 12 H6 M20 12 H22"/></svg></div>
    <div class="solution-title">Modular Platforms</div>
    <div class="solution-text">Lorem ipsum dolor sit amet, consectetur adipiscing elit, sed do eiusmod tempor incididunt ut labore et dolore magna aliqua. Ut enim ad ex ea commodo consequat.</div>
    <div class="solution-link">LEARN MORE <span class="btn-dot"></span></div>
  </div>
  <h2 class="section-title" style="left:51px;top:1132px"><span class="light">WHO</span> <span class="bold">ARE WE</span></h2>
  <span class="rule" style="left:51px;top:1158px"></span>
  <div class="copy" style="left:51px;top:1179px;width:220px">
    <p>We are engineers, architects, and technologists with a shared purpose: to align software precision with IT reality.</p>
    <p>Our team brings decades of experience in enterprise architecture, system integration, and software engineering. We believe technology should be both powerful and practical — imaginative yet grounded.</p>
    <p>Our DNA? Curiosity, clarity, and a relentless drive for quality.</p>
  </div>
  <span class="btn btn--learn" style="left:51px;top:1270px">LEARN MORE</span>
  <div class="who-photo"><div class="who-photo-inner" role="img" aria-label="Photo of illuminated server racks in a data centre"></div></div>
  <h2 class="section-title" style="left:0;width:551px;text-align:center;top:1393px"><span class="light">CONTACT</span> <span class="bold">US</span></h2>
  <div class="field" style="left:85px;top:1443px;width:187px">First Name *</div>
  <div class="field" style="left:279px;top:1443px;width:187px">Last Name *</div>
  <div class="field" style="left:85px;top:1473px;width:187px">Phone Number *</div>
  <div class="field" style="left:279px;top:1473px;width:187px">Email Address *</div>
  <div class="field field--message" style="left:85px;top:1505px;width:381px">Message</div>
  <span class="btn" style="left:239px;top:1567px;width:73px;height:21px">SUBMIT NOW</span>
  <div class="footer-logo"><span class="logo-mark"></span><span class="logo-name">QR.KA HORIZON</span></div>
  <div class="socials"><span class="social"></span><span class="social social--active"></span><span class="social"></span><span class="social"></span></div>
  <div class="foot-col" style="left:206px;top:1674px"><div class="foot-head">Quick Links</div>About<br>Products<br>Brands<br>Services<br>Contact</div>
  <div class="foot-col" style="left:289px;top:1674px"><div class="foot-head">About Company</div>GDPR<br>Privacy Policy<br>Cookie Policy<br>Terms &amp; Condition<br>Support</div>
  <div class="foot-col" style="left:389px;top:1674px;width:120px">
    <div class="foot-head">Contact Us</div>
    <div class="contact-item"><svg width="6" height="7" viewBox="0 0 6 7"><path d="M3 0.5a2.3 2.3 0 0 1 2.3 2.3C5.3 4.5 3 6.5 3 6.5S0.7 4.5 0.7 2.8A2.3 2.3 0 0 1 3 0.5z" fill="#0094D4"/></svg><b>Location</b><br>88 Larkfield Road, Unit 4, Brookhaven,<br>ST 20417</div>
    <div class="contact-item"><svg width="6" height="6" viewBox="0 0 6 6"><path d="M1 0.5 L2.2 0.5 L2.7 2 L2 2.6 Q2.7 3.6 3.4 4 L4 3.3 L5.5 3.8 L5.5 5 Q3 5.5 0.5 1.5z" fill="#0094D4"/></svg><b>Phone</b><br>+1 555 014 2290</div>
    <div class="contact-item"><svg width="6" height="5" viewBox="0 0 6 5"><rect x="0.3" y="0.5" width="5.4" height="4" fill="#0094D4"/><path d="M0.3 0.7 L3 2.7 L5.7 0.7" stroke="#0d0d0f" stroke-width="0.6" fill="none"/></svg><b>Email</b><br>info@qrkahorizon.example</div>
  </div>
  <span class="to-top"><svg width="7" height="5" viewBox="0 0 7 5"><path d="M1 4 L3.5 1.5 L6 4" stroke="#fff" stroke-width="1.2" fill="none"/></svg></span>
  <span class="foot-rule"></span>
  <p class="copyright">2025 Copyright - QR.KA Horizon. | All Rights Reserved</p>
</section>

<section class="page page--three">
  <div class="hero" role="img" aria-label="Photo of glowing lines of code in perspective over a dark blue background"></div>
  <svg class="bands" width="551" height="1818" viewBox="0 0 551 1818" aria-hidden="true">
    <path d="M0 263 Q275.5 343 551 263 V330 H0Z" fill="#E8F1F8"/>
    <path d="M0 518 Q275.5 438 551 518 V783 Q275.5 859 0 783Z" fill="#FFFFFF"/>
    <path d="M0 783 Q275.5 859 551 783 V1103 Q275.5 1019 0 1103Z" fill="#0591D3"/>
    <path d="M0 1103 Q275.5 1019 551 1103 V1323 Q275.5 1403 0 1323Z" fill="#FFFFFF"/>
    <path d="M0 1670 Q275.5 1590 551 1670 V1818 H0Z" fill="#0d0d0f"/>
  </svg>
  <div class="nav-logo"><span class="logo-mark"></span><span class="logo-name">QR.KA HORIZON</span></div>
  <span class="nav-menu nav-menu--home">HOME</span>
  <span class="nav-menu nav-menu--solutions">SOLUTIONS</span>
  <span class="nav-menu nav-menu--who">WHO ARE WE</span>
  <span class="btn btn--contact">CONTACT US</span>
  <div class="hero-copy">
    <h1 class="hero-title">QR.KA HORIZON</h1>
    <p class="hero-sub">Bridging Imagination, Software Engineering, and IT Infrastructure</p>
    <span class="btn btn--hero">GET STARTED <span class="btn-dot"></span></span>
  </div>
  <h2 class="section-title" style="left:0;width:551px;text-align:center;top:331px"><span class="light">WELCOME</span> <span class="bold">TO QR.KA HORIZON</span></h2>
  <div class="copy copy--center" style="left:66px;top:376px;width:419px">
    <p>QR.KA Horizon is where imagination meets execution. We unify the disciplines of software engineering and IT to deliver robust, future-oriented software solutions that are seamlessly integrated into diverse IT ecosystems.</p>
    <p>Our team thrives at the intersection of precision engineering and visionary architecture, ensuring every project is tailored, scalable, and secure. Whether optimizing legacy systems or deploying greenfield architectures, we believe that technology should not only work – it should inspire.</p>
    <p>At QR.KA Horizon, “Horizon” isn't about what you see — it's about what you imagine. Let's build the future together.</p>
  </div>
  <div class="architecture-graphic" role="img" aria-label="Architecture graphic of the ORBIT Layer product linking client apps, gateway, data lake, microservices and enterprise IT"></div>
  <h2 class="section-title" style="left:276px;top:537px"><span class="light">OUR</span> <span class="bold">PRODUCTS</span></h2>
  <span class="rule" style="left:276px;top:564px"></span>
  <div class="copy" style="left:275px;top:586px;width:226px">
    <p>ORBIT Layer™ is our flagship middleware that seamlessly connects diverse systems, enabling real-time data flow and business process synchronization.</p>
    <p>Whether cloud-native or hybrid, ORBIT adapts intelligently to your environment — secure, efficient, and built to scale.</p>
    <p>Introducing **FluxLink**, our modular architecture for synchronizing real-time data across hybrid systems.</p>
    <p>FluxLink allows seamless integration of microservices, legacy systems, and cloud platforms. It's scalable, resilient, and purpose-built to evolve with your IT ecosystem.</p>
  </div>
  <span class="btn btn--learn" style="left:275px;top:732px">LEARN MORE</span>
  <h2 class="section-title section-title--inverse" style="left:0;width:551px;text-align:center;top:846px"><span class="light">OUR</span> <span class="bold">SOLUTIONS</span></h2>
  <span class="rule rule--inverse" style="left:257px;top:873px"></span>
  <div class="solution" style="left:40px;top:894px">
    <div class="solution-icon"><svg width="26" height="26" viewBox="0 0 26 26" fill="none" stroke="#0054AA" stroke-width="1.2"><path d="M7 18 h12 a4 4 0 0 0 0-8 a6 6 0 0 0-11-1 a4.5 4.5 0 0 0-1 9z"/><circle cx="13" cy="14" r="3"/></svg></div>
    <div class="solution-title">Software-Defined Integration</div>
    <div class="solution-text">Lorem ipsum dolor sit amet, consectetur adipiscing elit, sed do eiusmod tempor incididunt ut labore et dolore magna aliqua. Ut enim ad ex ea commodo consequat.</div>
    <div class="solution-link">LEARN MORE <span class="btn-dot"></span></div>
  </div>
  <span class="divider"></span>
  <div class="solution" style="left:290px;top:894px">
    <div class="solution-icon"><svg width="26" height="26" viewBox="0 0 26 26" fill="none" stroke="#0054AA" stroke-width="1.2"><rect x="6" y="8" width="14" height="12" rx="1.5"/><circle cx="13" cy="14" r="3"/><path d="M9 8 V4 M17 8 V4 M4 12 H6 M20 12 H22"/></svg></div>
    <div class="solution-title">Modular Platforms</div>
    <div class="solution-text">Lorem ipsum dolor sit amet, consectetur adipiscing elit, sed do eiusmod tempor incididunt ut labore et dolore magna aliqua. Ut enim ad ex ea commodo consequat.</div>
    <div class="solution-link">LEARN MORE <span class="btn-dot"></span></div>
  </div>
  <h2 class="section-title" style="left:51px;top:1132px"><span class="light">WHO</span> <span class="bold">ARE WE</span></h2>
  <span class="rule" style="left:51px;top:1158px"></span>
  <div class="copy" style="left:51px;top:1179px;width:220px">
    <p>We are engineers, architects, and technologists with a shared purpose: to align software precision with IT reality.</p>
    <p>Our team brings decades of experience in enterprise architecture, system integration, and software engineering. We believe technology should be both powerful and practical — imaginative yet grounded.</p>
    <p>Our DNA? Curiosity, clarity, and a relentless drive for quality.</p>
  </div>
  <span class="btn btn--learn" style="left:51px;top:1270px">LEARN MORE</span>
  <div class="who-photo"><div class="who-photo-inner" role="img" aria-label="Photo of illuminated server racks in a data centre"></div></div>
  <h2 class="section-title" style="left:0;width:551px;text-align:center;top:1393px"><span class="light">CONTACT</span> <span class="bold">US</span></h2>
  <div class="field" style="left:85px;top:1443px;width:187px">First Name *</div>
  <div class="field" style="left:279px;top:1443px;width:187px">Last Name *</div>
  <div class="field" style="left:85px;top:1473px;width:187px">Phone Number *</div>
  <div class="field" style="left:279px;top:1473px;width:187px">Email Address *</div>
  <div class="field field--message" style="left:85px;top:1505px;width:381px">Message</div>
  <span class="btn" style="left:239px;top:1567px;width:73px;height:21px">SUBMIT NOW</span>
  <div class="footer-logo"><span class="logo-mark"></span><span class="logo-name">QR.KA HORIZON</span></div>
  <div class="socials"><span class="social"></span><span class="social social--active"></span><span class="social"></span><span class="social"></span></div>
  <div class="foot-col" style="left:206px;top:1674px"><div class="foot-head">Quick Links</div>About<br>Products<br>Brands<br>Services<br>Contact</div>
  <div class="foot-col" style="left:289px;top:1674px"><div class="foot-head">About Company</div>GDPR<br>Privacy Policy<br>Cookie Policy<br>Terms &amp; Condition<br>Support</div>
  <div class="foot-col" style="left:389px;top:1674px;width:120px">
    <div class="foot-head">Contact Us</div>
    <div class="contact-item"><svg width="6" height="7" viewBox="0 0 6 7"><path d="M3 0.5a2.3 2.3 0 0 1 2.3 2.3C5.3 4.5 3 6.5 3 6.5S0.7 4.5 0.7 2.8A2.3 2.3 0 0 1 3 0.5z" fill="#0094D4"/></svg><b>Location</b><br>88 Larkfield Road, Unit 4, Brookhaven,<br>ST 20417</div>
    <div class="contact-item"><svg width="6" height="6" viewBox="0 0 6 6"><path d="M1 0.5 L2.2 0.5 L2.7 2 L2 2.6 Q2.7 3.6 3.4 4 L4 3.3 L5.5 3.8 L5.5 5 Q3 5.5 0.5 1.5z" fill="#0094D4"/></svg><b>Phone</b><br>+1 555 014 2290</div>
    <div class="contact-item"><svg width="6" height="5" viewBox="0 0 6 5"><rect x="0.3" y="0.5" width="5.4" height="4" fill="#0094D4"/><path d="M0.3 0.7 L3 2.7 L5.7 0.7" stroke="#0d0d0f" stroke-width="0.6" fill="none"/></svg><b>Email</b><br>info@qrkahorizon.example</div>
  </div>
  <span class="to-top"><svg width="7" height="5" viewBox="0 0 7 5"><path d="M1 4 L3.5 1.5 L6 4" stroke="#fff" stroke-width="1.2" fill="none"/></svg></span>
  <span class="foot-rule"></span>
  <p class="copyright">2025 Copyright - QR.KA Horizon. | All Rights Reserved</p>
</section>

</body>
</html>
```